Business Cards Design for the electrical wholesaler: clean bold dynamic :)

We need a business card design that would follow our latest brand guidelines. As an electrical wholesaler we want to bring a fresh look and feel into the industry. The design should be clean bold and dynamic. It should come alive with the renewed energy of our green colour. Our grey colour should keep things balanced and complement the notion of maturity and responsibility. We employ Lato as a corporate font however are not bound by this font and we’re open to interpretation here.

Target Market(s)

Electrical contractors

Industry/Entity Type

Business

Contact Information for Business Card

Logo
Name & Surname: Halyna Dorosh
Job Title: Director of Marketing
Email: halya.dorosh@quillmail.example
Cell phone: 780.555.0139
Address: 20517 - 87 Ave. Edmonton, AB, Canada. T6K 4N8
Business Phone: 780.555.0184
Website: www.brovix.example

Font styles to use
Other font styles liked:
• Lato

Requirements
Must have
• Logo & website
Nice to have
• Brand elements - some of them you may find in the attached Brand Guidelines (e.g. three lines on the background signifying "W")

```html
<!DOCTYPE html>
<html lang="en">
<head>
<meta charset="utf-8">
<title>Brovix Business Card</title>
<link href="https://fonts.googleapis.com/css2?family=Exo+2:wght@500&family=Roboto:wght@400;500&display=swap" rel="stylesheet">
<style>
  :root {
    --backdrop: #4b4b4c;
    --backdrop-dark: #2e2e2f;
    --card: #1e1e1f;
    --card-edge: #151516;
    --green: #7ed321;
    --grey-light: #c9c9c9;
    --text: #f2f2f2;
    --icon-bg: #4a4a4c;
    --gloss: #2b2b2d;
  }
  * { box-sizing: border-box; margin: 0; padding: 0; }
  html, body { width: 799px; height: 1200px; overflow: hidden; }
  body {
    background: radial-gradient(ellipse at 60% 35%, var(--backdrop) 0%, var(--backdrop-dark) 100%);
    font-family: "Roboto", Arial, sans-serif;
    position: relative;
  }
  .card {
    position: absolute;
    left: 100px;
    width: 600px;
    height: 340px;
    border-radius: 24px;
    background: linear-gradient(160deg, #232324 0%, var(--card) 60%, var(--card-edge) 100%);
    box-shadow: 0 18px 40px rgba(0,0,0,0.45);
    overflow: hidden;
  }
  .card--front { top: 120px; }
  .card--back { top: 740px; }

  .brand-mark {
    position: absolute;
    display: flex;
    align-items: center;
    gap: 14px;
    font-family: "Roboto", Arial, sans-serif;
    font-weight: 500;
    letter-spacing: 1px;
    line-height: 1;
  }
  .brand-mark__square { width: 44px; height: 44px; border-radius: 6px; }
  .card--front .brand-mark {
    left: 150px; top: 138px;
    font-size: 72px;
    color: var(--gloss);
  }
  .card--front .brand-mark__square { background: var(--gloss); width: 56px; height: 56px; }

  .card--back .brand-mark {
    right: 40px; top: 62px;
    font-size: 54px;
    color: var(--green);
  }
  .card--back .brand-mark__square { background: var(--grey-light); }

  .contact {
    position: absolute;
    left: 40px; top: 140px;
    right: 30px;
    color: var(--text);
  }
  .contact__name {
    font-family: "Exo 2", Arial, sans-serif;
    font-weight: 500;
    font-size: 26px;
    line-height: 1.15;
    color: var(--green);
  }
  .contact__title { font-size: 15px; margin-top: 2px; margin-bottom: 12px; }
  .contact__list { list-style: none; font-size: 15px; }
  .contact__row { display: flex; align-items: center; gap: 20px; margin-top: 6px; white-space: nowrap; }
  .contact__item { display: flex; align-items: center; gap: 8px; }
  .contact__icon { width: 16px; height: 16px; flex: none; }
</style>
</head>
<body>
  <section class="card card--front">
    <div class="brand-mark"><span class="brand-mark__square"></span>brovix</div>
  </section>

  <section class="card card--back">
    <div class="brand-mark"><span class="brand-mark__square"></span>brovix</div>
    <div class="contact">
      <h1 class="contact__name">Halyna Dorosh</h1>
      <p class="contact__title">Director of Marketing</p>
      <ul class="contact__list">
        <li class="contact__row">
          <span class="contact__item">
            <svg class="contact__icon" viewBox="0 0 16 16"><circle cx="8" cy="8" r="8" fill="var(--icon-bg)"/><path d="M5 4.5h2l.7 2-1.1.8a5 5 0 0 0 2.1 2.1l.8-1.1 2 .7v2c0 .4-.4.7-.8.7A7 7 0 0 1 4.3 5.3c0-.4.3-.8.7-.8z" fill="var(--green)"/></svg>
            780.555.0184
          </span>
          <span class="contact__item">
            <svg class="contact__icon" viewBox="0 0 16 16"><circle cx="8" cy="8" r="8" fill="var(--icon-bg)"/><rect x="5.5" y="3.5" width="5" height="9" rx="1" fill="var(--green)"/><rect x="6.5" y="4.8" width="3" height="5.4" fill="var(--icon-bg)"/></svg>
            780.555.0139
          </span>
        </li>
        <li class="contact__row">
          <span class="contact__item">
            <svg class="contact__icon" viewBox="0 0 16 16"><circle cx="8" cy="8" r="8" fill="var(--icon-bg)"/><rect x="4" y="5" width="8" height="6" rx="1" fill="var(--green)"/><path d="M4.3 5.5 8 8.3l3.7-2.8" stroke="var(--icon-bg)" stroke-width="1" fill="none"/></svg>
            halya.dorosh@quillmail.example
          </span>
          <span class="contact__item">
            <svg class="contact__icon" viewBox="0 0 16 16"><circle cx="8" cy="8" r="8" fill="var(--icon-bg)"/><circle cx="8" cy="8" r="4" fill="none" stroke="var(--green)" stroke-width="1.2"/><path d="M4 8h8M8 4c-1.6 2.4-1.6 5.6 0 8M8 4c1.6 2.4 1.6 5.6 0 8" stroke="var(--green)" stroke-width="1" fill="none"/></svg>
            www.brovix.example
          </span>
        </li>
        <li class="contact__row">20517 - 87 Ave. Edmonton, AB, Canada. T6K 4N8</li>
      </ul>
    </div>
  </section>
</body>
</html>
```